BRIGHT RIVER POWER.

I'd like my business logo.
contact name: Dennis Halvorsen
phone:0438759164
email: info@brightriverpower.net.au
website: www.brightriverpower.net.au

services:
solar
battery storage
LED lighting
energy saving solutions
general electrical
I'd like the design to look professional

Target Market(s)

Everyone

Industry/Entity Type

Business

Contact Information for Business Card

as described above

Requirements
Must have
• Id like the colours and the design to work well with my logo.

```html
<!DOCTYPE html>
<html lang="en">
<head>
<meta charset="UTF-8">
<title>Bright River Power – Business Card</title>
<link href="https://fonts.googleapis.com/css2?family=Source+Sans+3:wght@400;600;700&display=swap" rel="stylesheet">
<style>
  :root {
    --backdrop: #3a3533;
    --card: #0c0c0c;
    --card-edge: #1c1c1c;
    --text: #e8e8e8;
    --text-soft: #c9c9c9;
    --silver: #d4d4d4;
    --amber: #f2a81d;
    --leaf: #7cc242;
    --divider: #2a2a2a;
  }
  * { box-sizing: border-box; margin: 0; padding: 0; }
  html, body {
    width: 1200px; height: 900px; overflow: hidden;
    background: var(--backdrop);
    font-family: "Source Sans 3", "Myriad Pro", Arial, sans-serif;
  }
  .canvas {
    position: relative; width: 1200px; height: 900px;
    display: flex; align-items: center; justify-content: center; gap: 60px;
  }
  .card {
    position: relative; width: 525px; height: 300px;
    background: var(--card);
    border: 1px solid var(--card-edge);
    box-shadow: 0 14px 30px rgba(0,0,0,.45);
    color: var(--text);
  }
  /* front */
  .card--front { display: flex; }
  .brand-block {
    width: 45%; display: flex; flex-direction: column;
    align-items: center; justify-content: center; gap: 14px;
  }
  .brand-mark {
    width: 64px; height: 64px; border-radius: 50%;
    background: var(--leaf);
  }
  .brand-name {
    font-weight: 700; font-size: 21px; letter-spacing: 2px;
    color: var(--amber); text-align: center; line-height: 1.25;
  }
  .front-divider {
    width: 1px; margin: 40px 0; background: var(--divider);
  }
  .contact-block {
    flex: 1; padding: 0 28px; display: flex; flex-direction: column; justify-content: center;
  }
  .contact-name {
    font-weight: 700; font-size: 19px; color: var(--amber); margin-bottom: 16px;
  }
  .contact-list { list-style: none; }
  .contact-list li {
    display: flex; align-items: center; gap: 10px;
    font-size: 15px; line-height: 1.45; color: var(--text);
  }
  .contact-list svg { width: 11px; height: 11px; flex: none; }
  /* back */
  .card--back {
    display: flex; flex-direction: column; align-items: center; justify-content: center;
  }
  .back-brand {
    font-weight: 700; font-size: 30px; letter-spacing: 3px;
    color: var(--silver); margin-bottom: 30px;
  }
  .services-title {
    font-weight: 700; font-size: 14px; letter-spacing: .5px;
    color: var(--text); margin-bottom: 10px;
  }
  .services-line {
    font-size: 14px; color: var(--text-soft); line-height: 1.5;
  }
</style>
</head>
<body>
<main class="canvas">
  <section class="card card--front" aria-label="Business card front">
    <div class="brand-block">
      <span class="brand-mark" aria-hidden="true"></span>
      <span class="brand-name">BRIGHT RIVER<br>POWER</span>
    </div>
    <div class="front-divider"></div>
    <div class="contact-block">
      <p class="contact-name">Dennis Halvorsen</p>
      <ul class="contact-list">
        <li>
          <svg viewBox="0 0 12 12" aria-hidden="true"><path fill="#f2a81d" d="M2.5 0.8 4.2 3.2 3.2 4.4c.8 1.7 2.1 3 3.8 3.8l1.2-1 2.4 1.7-.8 2.3C5.2 10.9 1 6.7.3 1.6z"/></svg>
          0438759164
        </li>
        <li>
          <svg viewBox="0 0 12 12" aria-hidden="true"><rect x="0.5" y="2" width="11" height="8" fill="#f2a81d"/><path d="M0.5 2 6 6.5 11.5 2" fill="none" stroke="#0c0c0c" stroke-width="1"/></svg>
          info@brightriverpower.net.au
        </li>
        <li>
          <svg viewBox="0 0 12 12" aria-hidden="true"><circle cx="6" cy="6" r="5.5" fill="#f2a81d"/><path d="M.5 6h11M6 .5c-2.5 3-2.5 8 0 11M6 .5c2.5 3 2.5 8 0 11" fill="none" stroke="#0c0c0c" stroke-width=".8"/></svg>
          www.brightriverpower.net.au
        </li>
      </ul>
    </div>
  </section>

  <section class="card card--back" aria-label="Business card back">
    <p class="back-brand">BRIGHT RIVER POWER</p>
    <p class="services-title">WHAT I DO</p>
    <p class="services-line">Solar | Battery Storage</p>
    <p class="services-line">LED Lighting | Energy Saving Solutions</p>
  </section>
</main>
</body>
</html>
```